Gobal construction supply company needs new business card design

I need a business card design for my global supply company using an existing logo. i will be looking to print these on rounded corner cards with the black background version of my logo on the back. on the front white background, my logo again and my simple details.

```html
<!DOCTYPE html>
<html lang="en">
<head>
<meta charset="utf-8">
<title>Northvale Supply – Business Card</title>
<link rel="stylesheet" href="https://fonts.googleapis.com/css2?family=Montserrat:wght@700&family=Open+Sans:wght@400;700&display=swap">
<style>
  :root {
    --stage: #3a3a3a;
    --card-white: #f8f8f8;
    --brand-red: #d90000;
    --ink: #111111;
    --text-grey: #333333;
  }
  html, body {
    margin: 0;
    padding: 0;
    width: 1200px;
    height: 782px;
    overflow: hidden;
    background: var(--stage);
  }
  .canvas {
    position: relative;
    width: 1200px;
    height: 782px;
  }
  .card {
    position: absolute;
    top: 242px;
    width: 520px;
    height: 297px;
    overflow: hidden;
    box-shadow: 0 8px 24px rgba(0,0,0,0.45);
  }
  .card-front { left: 50px; background: var(--card-white); }
  .card-back  { left: 630px; background: var(--brand-red); }

  .holder {
    position: absolute;
    left: 30px;
    top: 28px;
    white-space: nowrap;
  }
  .holder-name {
    font-family: "Montserrat", sans-serif;
    font-weight: 700;
    font-size: 17px;
    color: var(--brand-red);
    letter-spacing: 0.3px;
    margin: 0;
  }
  .holder-title {
    font-family: "Open Sans", sans-serif;
    font-size: 12px;
    color: var(--text-grey);
    margin: 0;
  }

  .phones {
    position: absolute;
    left: 30px;
    top: 160px;
    font-family: "Open Sans", sans-serif;
    font-size: 13px;
    color: var(--text-grey);
    line-height: 18px;
    white-space: nowrap;
  }
  .contact-line { display: flex; align-items: center; gap: 6px; }
  .contact-line svg { width: 10px; height: 10px; flex: none; }

  .brand {
    position: absolute;
    left: 238px;
    top: 150px;
    display: flex;
    align-items: center;
    gap: 9px;
    white-space: nowrap;
  }
  .brand-name {
    font-family: "Open Sans", sans-serif;
    font-weight: 700;
    font-size: 22px;
    line-height: 1;
    color: var(--ink);
    letter-spacing: 0.4px;
  }
  .brand-dot {
    width: 15px;
    height: 15px;
    border-radius: 50%;
    background: var(--brand-red);
    flex: none;
  }

  .web-contacts {
    position: absolute;
    right: 22px;
    top: 212px;
    font-family: "Open Sans", sans-serif;
    font-size: 13px;
    color: var(--text-grey);
    line-height: 18px;
    text-align: right;
    white-space: nowrap;
  }
  .web-contacts .contact-line { justify-content: flex-end; }

  .front-bands {
    position: absolute;
    left: 0;
    top: 0;
    width: 520px;
    height: 297px;
  }

  .back-brand {
    position: absolute;
    inset: 0;
    display: flex;
    align-items: center;
    justify-content: center;
    gap: 9px;
    white-space: nowrap;
  }
  .back-brand .brand-name { color: #ffffff; font-size: 22px; }
  .back-brand .brand-dot { background: #ffffff; width: 13px; height: 13px; }
</style>
</head>
<body>
<main class="canvas">

  <section class="card card-front" aria-label="Business card front">
    <svg class="front-bands" viewBox="0 0 520 297" aria-hidden="true">
      <polygon points="0,250 126,250 142,297 0,297" fill="var(--ink)"/>
      <polygon points="150,262 520,278 520,297 162,297" fill="var(--brand-red)"/>
    </svg>

    <div class="holder">
      <p class="holder-name">MARCUS HALE</p>
      <p class="holder-title">Managing Director</p>
    </div>

    <div class="phones">
      <div class="contact-line">
        <svg viewBox="0 0 10 10"><path d="M1 3 Q1 1 3 1 L7 1 Q9 1 9 3 L9 4 L7 4 L7 3 L3 3 L3 4 L1 4 Z M2 5 L8 5 L9 9 L1 9 Z" fill="var(--brand-red)"/></svg>
        <span>055-870 214 356</span>
      </div>
      <div class="contact-line">
        <svg viewBox="0 0 10 10"><rect x="2" y="0.5" width="6" height="9" rx="1" fill="none" stroke="var(--brand-red)" stroke-width="1.4"/></svg>
        <span>055-870 214 356</span>
      </div>
    </div>

    <div class="brand">
      <span class="brand-name">NORTHVALE SUPPLY</span>
      <span class="brand-dot"></span>
    </div>

    <div class="web-contacts">
      <div class="contact-line">
        <span>info@northvale.com</span>
        <svg viewBox="0 0 10 10"><rect x="0.5" y="2" width="9" height="6.5" fill="var(--brand-red)"/><path d="M0.5 2 L5 6 L9.5 2" fill="none" stroke="#fff" stroke-width="0.9"/></svg>
      </div>
      <div class="contact-line">
        <span>www.northvale.com</span>
        <svg viewBox="0 0 10 10"><circle cx="5" cy="5" r="4.5" fill="var(--brand-red)"/><path d="M1 5 H9 M5 0.5 Q2.5 5 5 9.5 M5 0.5 Q7.5 5 5 9.5" fill="none" stroke="#fff" stroke-width="0.7"/></svg>
      </div>
    </div>
  </section>

  <section class="card card-back" aria-label="Business card back">
    <div class="back-brand">
      <span class="brand-name">NORTHVALE SUPPLY</span>
      <span class="brand-dot"></span>
    </div>
  </section>

</main>
</body>
</html>
```